Business Card Design

New business card design

Target Market(s)

Residential & Commercial Property Managers

Industry/Entity Type

Plumbing Services

Contact Information for Business Card

Name - Rowan Keddle, title - Director, Phone Number - 0431 286 517, email - rowan@tbk-plumbing.com.au, Company ABN - 73 215 904 386,

Font styles to use
Sans Serif

Colors
0054AA
0677BA
7BADD7
CADEEF
E8F1F8

```html
<!DOCTYPE html>
<html lang="en">
<head>
<meta charset="utf-8">
<title>TBK Plumbing Services – Business Card</title>
<link href="https://fonts.googleapis.com/css2?family=Montserrat:wght@300;400;500;700&display=swap" rel="stylesheet">
<style>
  :root {
    --backdrop: #23292f;
    --card-white: #ffffff;
    --navy: #1e252c;
    --brand-blue: #29a3dc;
    --ink: #1b1f24;
    --muted: #6b747c;
  }
  * { box-sizing: border-box; margin: 0; padding: 0; }
  html, body {
    width: 1200px; height: 900px; overflow: hidden;
    background: var(--backdrop);
    font-family: "Montserrat", sans-serif;
  }
  .stage {
    width: 1200px; height: 900px;
    display: flex; align-items: center; justify-content: center;
  }
  .card {
    position: relative;
    width: 1000px; height: 572px;
    background: var(--card-white);
    border-radius: 36px;
    overflow: hidden;
    box-shadow: 0 24px 60px rgba(0,0,0,.45);
  }
  .card__swoosh {
    position: absolute; left: 0; top: 0;
    width: 100%; height: 100%;
  }
  .brand {
    position: absolute;
    left: 64px; top: 196px;
    width: 420px;
    display: flex; align-items: center; gap: 14px;
    white-space: nowrap;
  }
  .brand__dot {
    width: 20px; height: 20px; border-radius: 50%;
    background: var(--brand-blue);
    flex: none;
  }
  .brand__name {
    font-weight: 500;
    font-size: 25px;
    letter-spacing: 0.04em;
    color: var(--ink);
  }
  .divider {
    position: absolute;
    left: 515px; top: 160px;
    width: 2px; height: 220px;
    background: var(--brand-blue);
  }
  .contact {
    position: absolute;
    left: 555px; top: 165px;
    color: var(--ink);
    white-space: nowrap;
  }
  .contact__name {
    font-weight: 700;
    font-size: 34px;
    color: var(--brand-blue);
    line-height: 1.1;
  }
  .contact__title {
    font-size: 22px; font-weight: 400;
    margin-top: 4px;
  }
  .contact__abn {
    font-size: 21px; font-weight: 400;
    margin-top: 22px;
  }
  .contact__abn-label { color: var(--brand-blue); font-weight: 300; }
  .contact__line {
    display: flex; align-items: center; gap: 12px;
    font-size: 21px; font-weight: 400;
    margin-top: 16px;
  }
  .contact__icon { width: 18px; height: 18px; flex: none; }
</style>
</head>
<body>
<main class="stage">
  <article class="card">
    <svg class="card__swoosh" viewBox="0 0 1000 572" preserveAspectRatio="none" aria-hidden="true">
      <path d="M0 318 C 260 470, 600 560, 880 572 L0 572 Z" fill="#1e252c"/>
      <path d="M20 330 C 280 470, 600 548, 880 566" fill="none" stroke="#29a3dc" stroke-width="5"/>
    </svg>

    <div class="brand">
      <span class="brand__dot"></span>
      <span class="brand__name">TBK Plumbing Services</span>
    </div>

    <div class="divider"></div>

    <section class="contact">
      <h1 class="contact__name">Rowan Keddle</h1>
      <p class="contact__title">Director</p>
      <p class="contact__abn"><span class="contact__abn-label">ABN</span> - 73 215 904 386</p>
      <p class="contact__line">
        <svg class="contact__icon" viewBox="0 0 24 24" aria-hidden="true">
          <path d="M6.6 10.8c1.4 2.8 3.8 5.1 6.6 6.6l2.2-2.2c.3-.3.7-.4 1-.2 1.1.4 2.3.6 3.6.6.6 0 1 .4 1 1V20c0 .6-.4 1-1 1C10.6 21 3 13.4 3 4c0-.6.4-1 1-1h3.5c.6 0 1 .4 1 1 0 1.300.2 2.500.6 3.600.1.300 0 .700-.2 1l-2.3 2.2z" fill="#29a3dc"/>
        </svg>
        0431 286 517
      </p>
      <p class="contact__line">
        <svg class="contact__icon" viewBox="0 0 24 24" aria-hidden="true">
          <rect x="2" y="5" width="20" height="14" rx="1.5" fill="#29a3dc"/>
          <path d="M3 6l9 7 9-7" fill="none" stroke="#fff" stroke-width="1.6"/>
        </svg>
        rowan@tbk-plumbing.com.au
      </p>
    </section>
  </article>
</main>
</body>
</html>
```